Realtor branding business card

modern, simple and self branding. Broker office logo needs to be used but not emphasized. Looking to brand myself

Target Market(s)

buyers, sellers and investors

Industry/Entity Type

Realtor

Contact Information for Business Card

Sample of my current business card on file

Requirements
Must have
• my website - tobiasmerrowkl.com
• Realtor logo
• Fair housing logo
Nice to have
• Colors from office logo but not a must
Should not have
• Do not want headshot

```html
<!DOCTYPE html>
<html lang="en">
<head>
<meta charset="utf-8">
<title>Tobias Merrow – Realtor Business Card</title>
<link rel="stylesheet" href="https://fonts.googleapis.com/css2?family=Montserrat:wght@400;500;700&display=swap">
<style>
  :root {
    --bg: #161616;
    --card: #262626;
    --card-edge: #2f2f2f;
    --brand-blue: #2f2a8c;
    --name-blue: #4a42c0;
    --accent-red: #d8262c;
    --text-light: #f2f2f2;
    --icon-grey: #8a8a9a;
    --badge-grey: #6d6d78;
  }
  * { box-sizing: border-box; margin: 0; padding: 0; }
  html, body {
    width: 1200px; height: 900px; overflow: hidden;
    background: var(--bg);
    font-family: "Montserrat", sans-serif;
  }
  .canvas {
    width: 1200px; height: 900px;
    display: flex; flex-direction: column;
    align-items: center; justify-content: center; gap: 44px;
  }
  .card {
    position: relative;
    width: 660px; height: 377px;
    background: linear-gradient(135deg, var(--card) 0%, var(--card-edge) 70%, var(--card) 100%);
    border-bottom: 6px solid var(--brand-blue);
    box-shadow: 0 18px 40px rgba(0,0,0,0.55);
  }
  .broker-name {
    color: var(--brand-blue);
    font-weight: 700;
    line-height: 1.1;
    display: flex; align-items: center; gap: 12px;
  }
  .broker-mark {
    width: 14px; height: 14px; background: var(--accent-red); flex: none;
  }

  /* Front */
  .card-front { display: flex; flex-direction: column; align-items: center; justify-content: center; }
  .card-front .broker-name { font-size: 34px; margin-bottom: 30px; }
  .front-url {
    position: absolute; bottom: 46px; left: 0; right: 0;
    text-align: center; font-size: 18px; color: var(--text-light); letter-spacing: 0.3px;
  }
  .front-url .domain { color: var(--accent-red); font-weight: 500; }

  /* Back */
  .card-back { display: flex; align-items: center; }
  .back-brand { width: 320px; padding-left: 44px; }
  .card-back .broker-name { font-size: 26px; }
  .divider {
    width: 2px; height: 250px; background: var(--accent-red); margin-right: 32px;
  }
  .agent { color: var(--text-light); }
  .agent-name {
    color: var(--name-blue); font-weight: 700; font-size: 26px;
    text-transform: uppercase; letter-spacing: 0.5px; line-height: 1.15;
  }
  .agent-title { font-size: 17px; margin-bottom: 16px; }
  .contact-list { list-style: none; font-size: 16px; line-height: 1.6; }
  .contact-list li { display: flex; align-items: center; gap: 12px; }
  .contact-list svg { width: 14px; height: 14px; flex: none; }
  .address { margin-top: 12px; font-size: 16px; line-height: 1.45; }

  .badges {
    position: absolute; left: 44px; bottom: 28px;
    display: flex; gap: 14px; align-items: center;
  }
  .badge { width: 30px; height: 30px; background: var(--badge-grey); }
  .badge-round { border-radius: 50%; }
</style>
</head>
<body>
<main class="canvas">

  <section class="card card-front" aria-label="Card front">
    <div class="broker-name"><span class="broker-mark"></span><span>Brightfield<br>Realty Group</span></div>
    <p class="front-url">www.<span class="domain">tobiasmerrowkl</span>.com</p>
  </section>

  <section class="card card-back" aria-label="Card back">
    <div class="back-brand">
      <div class="broker-name"><span class="broker-mark"></span><span>Brightfield<br>Realty Group</span></div>
    </div>
    <div class="divider"></div>
    <div class="agent">
      <h1 class="agent-name">Tobias Merrow</h1>
      <p class="agent-title">Realtor</p>
      <ul class="contact-list">
        <li>
          <svg viewBox="0 0 14 14" aria-hidden="true"><rect x="3.5" y="1" width="7" height="12" rx="1.2" fill="none" stroke="var(--icon-grey)" stroke-width="1.3"/></svg>
          407. 555. 0142
        </li>
        <li>
          <svg viewBox="0 0 14 14" aria-hidden="true"><path d="M3 1.5 L5.5 4 L4.2 5.6 C5 7.4 6.6 9 8.4 9.8 L10 8.5 L12.5 11 L11 12.5 C6 12 2 8 1.5 3 Z" fill="var(--icon-grey)"/></svg>
          407. 555. 0187
        </li>
        <li>
          <svg viewBox="0 0 14 14" aria-hidden="true"><rect x="1" y="3" width="12" height="8.5" fill="none" stroke="var(--icon-grey)" stroke-width="1.2"/><path d="M1 3 L7 8 L13 3" fill="none" stroke="var(--icon-grey)" stroke-width="1.2"/></svg>
          info@tobiasmerrowkl.com
        </li>
        <li>
          <svg viewBox="0 0 14 14" aria-hidden="true"><circle cx="7" cy="7" r="5.6" fill="none" stroke="var(--icon-grey)" stroke-width="1.2"/><ellipse cx="7" cy="7" rx="2.4" ry="5.6" fill="none" stroke="var(--icon-grey)" stroke-width="1"/><path d="M1.4 7 H12.6" stroke="var(--icon-grey)" stroke-width="1"/></svg>
          www.tobiasmerrowkl.com
        </li>
      </ul>
      <p class="address">48 Larkspur Avenue<br>Cedar Hollow, FL 32790</p>
    </div>
    <div class="badges">
      <span class="badge" role="img" aria-label="Realtor association badge"></span>
      <span class="badge badge-round" role="img" aria-label="Equal housing opportunity badge"></span>
    </div>
  </section>

</main>
</body>
</html>
```